Home Security Company Business Card

Looking for a eye catching business card that is non traditional and stands out but yet still looks professional. It should include all the pertinent information such as name, title, address, telephone, e-mail, website address should definitely stand out and then finally the logo.

Target Market(s)

Residential and Commercial accounts mostly upscale accounts

Industry/Entity Type

Security

Contact Information for Business Card

Name
Title
Address
Office #
Cell #
E-mail
Website

Font styles to use
Serif
Sans Serif

Requirements
Must have
• Logo, two sided color configuration
Nice to have
• You decide
Should not have
• There really aren't any.

```html
<!DOCTYPE html>
<html lang="en">
<head>
<meta charset="utf-8">
<title>Bulwark Home Protection – Business Card</title>
<link rel="stylesheet" href="https://fonts.googleapis.com/css2?family=Lato:wght@400;700;900&display=swap">
<style>
  :root {
    --backdrop: #2b2b2b;
    --card-white: #f7f7f7;
    --maroon: #6e0d06;
    --maroon-deep: #5a0903;
    --gold: #d6a83a;
    --cream: #f4ece4;
    --brand: #8a1a12;
  }
  * { box-sizing: border-box; margin: 0; padding: 0; }
  html, body {
    width: 1200px; height: 997px; overflow: hidden;
    background: radial-gradient(ellipse at 55% 50%, #3a3a3a 0%, var(--backdrop) 70%, #1c1c1c 100%);
    font-family: "Lato", sans-serif;
  }
  .card {
    position: absolute;
    width: 620px; height: 354px;
    background: var(--card-white);
    box-shadow: 0 18px 40px rgba(0,0,0,.55);
    overflow: hidden;
  }
  .card svg.band { position: absolute; inset: 0; width: 100%; height: 100%; }
  .card--front { left: 90px; top: 110px; }
  .card--back  { left: 490px; top: 530px; }

  .brand {
    position: absolute;
    display: flex; align-items: center; gap: 14px;
    color: var(--brand);
    font-weight: 900;
    text-transform: uppercase;
    letter-spacing: .5px;
    line-height: 1.05;
  }
  .brand__mark {
    width: 22px; height: 22px; border-radius: 50%;
    background: var(--brand); flex: none;
  }
  .card--front .brand { left: 150px; top: 92px; font-size: 30px; }
  .card--back  .brand { left: 150px; top: 62px; font-size: 28px; }

  .slogan {
    position: absolute; left: 190px; top: 286px;
    color: var(--cream);
    font-size: 13px; letter-spacing: 9px; text-transform: uppercase;
    transform: rotate(-12deg); transform-origin: left center;
    white-space: nowrap;
  }

  .person { position: absolute; left: 70px; top: 270px; color: var(--cream); }
  .person__name { font-size: 24px; font-weight: 900; letter-spacing: -.3px; }
  .person__title { font-size: 14px; margin-top: 2px; padding-left: 56px; }

  .contacts {
    position: absolute; right: 36px; top: 198px;
    list-style: none; color: var(--cream);
    font-size: 15px; line-height: 27px;
  }
  .contacts li { display: flex; align-items: center; gap: 10px; }
  .contacts svg { width: 16px; height: 16px; fill: var(--cream); flex: none; }
</style>
</head>
<body>

<section class="card card--front" aria-label="Card front">
  <svg class="band" viewBox="0 0 620 354" preserveAspectRatio="none" aria-hidden="true">
    <path d="M0 354 L0 318 Q330 270 620 120 L620 354 Z" fill="var(--maroon)"/>
    <path d="M0 318 Q330 270 620 120" fill="none" stroke="var(--gold)" stroke-width="4"/>
  </svg>
  <div class="brand"><span class="brand__mark"></span><span>Bulwark<br>Home Protection Inc.</span></div>
  <p class="slogan">Your solgan here</p>
</section>

<section class="card card--back" aria-label="Card back">
  <svg class="band" viewBox="0 0 620 354" preserveAspectRatio="none" aria-hidden="true">
    <path d="M0 260 Q330 190 620 150 L620 354 L0 354 Z" fill="var(--maroon)"/>
    <path d="M0 260 Q330 190 620 150" fill="none" stroke="var(--gold)" stroke-width="4"/>
  </svg>
  <div class="brand"><span class="brand__mark"></span><span>Bulwark<br>Home Protection Inc.</span></div>

  <div class="person">
    <p class="person__name">MARCUS HALE</p>
    <p class="person__title">Vet Director</p>
  </div>

  <ul class="contacts">
    <li><svg viewBox="0 0 16 16"><path d="M3 2h3l1.5 3.5-2 1.2a8 8 0 0 0 3.8 3.8l1.2-2L14 10v3a1 1 0 0 1-1 1A11 11 0 0 1 2 3a1 1 0 0 1 1-1z"/></svg>(03) 5550 0148</li>
    <li><svg viewBox="0 0 16 16"><path d="M1 3h14v10H1z M2 4l6 5 6-5" fill="none" stroke="var(--cream)" stroke-width="1.5"/></svg>office@bulwarkprotect.com.au</li>
    <li><svg viewBox="0 0 16 16"><path d="M6.5 9.5l3-3M7 4l1.5-1.5a2.8 2.8 0 0 1 4 4L11 8M9 12l-1.5 1.5a2.8 2.8 0 0 1-4-4L5 8" fill="none" stroke="var(--cream)" stroke-width="1.6"/></svg>www.bulwarkprotect.com.au</li>
    <li><svg viewBox="0 0 16 16"><path d="M8 1.5L1 8h2v6.5h4v-4h2v4h4V8h2z"/></svg>48 Elm Rd Ashbury VIC 3999</li>
  </ul>
</section>

</body>
</html>
```